Tiny Meadow Product Label for Tear-Free Head-to-Toe Wash

Need a bottle label design for a new line of natural products targeting infants and children. Products are Pediatrician-developed and paraben-free, sulfate-free, fragrance-free, and cruelty-free. Design should be clean and have a high-end feel to it. Will need other product labels in Tiny Meadow line designed as well in upcoming projects.

Target Market(s)

Newborn to young elementary age children and their parents

Industry/Entity Type

Cosmetics/Beauty

Font styles to use
Other font styles liked:
• Brand fonts are Jost and Sonorous

Colors

Designer to choose colors to be used in the design.

Requirements
Must have
• Tiny Meadow logo, Pediatrician Developed logo, and a clean high-end feel to it. The label must fit the specialty bottle we will be using (label measurements and diagram will be provided) for the front and back of bottle only (NOT the side labels). It must include our list of ingredients (will provide once designer selected).
Nice to have
• Should stand out on the shelf of other baby products due to it's clean simplicity and high-end feel
Should not have
• too much of a "kiddie" feel to it (targeting the parents not the kids)

```html
<!DOCTYPE html>
<html lang="en">
<head>
<meta charset="UTF-8">
<title>Tiny Meadow – Tear-Free Head-to-Toe Wash Labels</title>
<link rel="stylesheet" href="https://fonts.googleapis.com/css2?family=Quicksand:wght@700&family=Montserrat:wght@600&family=Roboto:ital,wght@0,500;1,400;1,700&family=Arimo:wght@400&display=swap">
<style>
  :root {
    --canvas: #ecebe8;
    --label: #fbf9f6;
    --gold: #9a7230;
    --gold-soft: #f3ede2;
    --ink: #222222;
    --white: #ffffff;
  }
  * { margin: 0; padding: 0; box-sizing: border-box; }
  html, body { width: 1200px; height: 1200px; overflow: hidden; }
  body { background: var(--canvas); position: relative; font-family: "Arimo", sans-serif; color: var(--ink); }

  .label {
    position: absolute;
    top: 270px;
    width: 460px;
    height: 660px;
    background: var(--label);
    border-radius: 80px 80px 0 0 / 96px 96px 0 0;
  }
  .label--front { left: 110px; }
  .label--back { left: 630px; }

  /* Front */
  .brand-mark {
    position: absolute; left: 137px; top: 42px;
    width: 186px; height: 186px; border-radius: 50%;
    border: 5px solid var(--gold); background: var(--label);
  }
  .brand-name {
    position: absolute; left: 0; right: 0; top: 236px;
    text-align: center; font-family: "Quicksand", sans-serif; font-weight: 700;
    font-size: 56px; letter-spacing: 1px; color: var(--ink); line-height: 1;
  }
  .tagline {
    position: absolute; left: 0; right: 0; top: 318px;
    text-align: center; font-family: "Montserrat", sans-serif; font-weight: 600;
    font-size: 13px; letter-spacing: 3.4px; color: var(--gold);
  }
  .product-band {
    position: absolute; left: 0; right: 0; top: 372px; height: 89px;
    background: var(--gold); color: var(--white);
    display: flex; flex-direction: column; justify-content: center; align-items: center;
    font-family: "Roboto", sans-serif; font-weight: 500; font-size: 28px; line-height: 1.2;
  }
  .product-claim {
    position: absolute; left: 0; right: 0; top: 472px;
    text-align: center; font-family: "Roboto", sans-serif; font-style: italic;
    font-size: 22px; color: var(--gold);
  }
  .free-badges {
    position: absolute; left: 0; right: 0; top: 533px;
    display: flex; justify-content: center; gap: 18px;
  }
  .free-badge {
    width: 56px; height: 56px; border-radius: 50%;
    border: 2px solid var(--gold); background: var(--gold-soft);
  }
  .net-weight {
    position: absolute; left: 0; right: 0; top: 613px;
    text-align: center; font-family: "Roboto", sans-serif; font-weight: 500;
    font-size: 20px; color: var(--gold);
  }

  /* Back */
  .brand-mark--small {
    position: absolute; left: 207px; top: 35px;
    width: 48px; height: 48px; border-radius: 50%;
    border: 2.5px solid var(--gold);
  }
  .back-copy {
    position: absolute; left: 62px; width: 336px;
    font-size: 17.5px; line-height: 23.5px; text-align: justify;
    text-align-last: center;
  }
  .intro { top: 102px; }
  .directions-text { top: 266px; }
  .ingredients-text { top: 408px; }
  .section-pill {
    position: absolute; left: 154px; width: 152px; height: 25px;
    border-radius: 13px; background: var(--gold); color: var(--white);
    font-size: 17px; line-height: 25px; text-align: center;
  }
  .pill-directions { top: 236px; }
  .pill-ingredients { top: 378px; }
  .maker {
    position: absolute; left: 62px; top: 550px;
    font-size: 17.5px; line-height: 23.5px;
  }
  .maker-title { font-family: "Roboto", sans-serif; font-weight: 700; font-style: italic; color: var(--gold); }
  .pediatrician-badge {
    position: absolute; left: 326px; top: 539px;
    width: 78px; height: 78px; border-radius: 50%;
    border: 2px solid var(--gold); background: var(--gold-soft);
  }
</style>
</head>
<body>
  <section class="label label--front">
    <div class="brand-mark"></div>
    <div class="brand-name">Tiny Meadow</div>
    <div class="tagline">NATURALLY, FOR EVERY BABY</div>
    <div class="product-band">
      <span>Tear-Free</span>
      <span>Head-to-Toe Wash</span>
    </div>
    <div class="product-claim">Naturally formulated for delicate skin</div>
    <div class="free-badges">
      <div class="free-badge" role="img" aria-label="Paraben free badge"></div>
      <div class="free-badge" role="img" aria-label="Sulfate free badge"></div>
      <div class="free-badge" role="img" aria-label="Fragrance free badge"></div>
      <div class="free-badge" role="img" aria-label="Cruelty free badge"></div>
    </div>
    <div class="net-weight">Net wt: 73 mL/2,43 fl.oz</div>
  </section>

  <section class="label label--back">
    <div class="brand-mark--small"></div>
    <p class="back-copy intro">A gentle, all-in-one cleanser made with natural ingredients to protect and nourish baby’s delicate hair and skin. Pediatrician-developed and suitable for daily use from newborn onwards.</p>
    <div class="section-pill pill-directions">Directions:</div>
    <p class="back-copy directions-text">Dispense a small amount into hands or washcloth. Gently massage into wet hair and skin. Rinse thoroughly. Avoid contact with eyes.</p>
    <div class="section-pill pill-ingredients">Ingredients:</div>
    <p class="back-copy ingredients-text">Aqua, Glycerin, Decyl Glucoside, Sodium Lauroyl Lactylate, Coco-Glucoside, Glyceryl Oleate, Xanthan Gum, Sodium Benzoate, Citric Acid. (Full list to be finalized.)</p>
    <div class="maker">
      <div class="maker-title">Manufactured for</div>
      <div>Tiny Meadow Co.</div>
      <div>tinymeadow.com/Made in USA</div>
    </div>
    <div class="pediatrician-badge" role="img" aria-label="Pediatrician developed badge"></div>
  </section>
</body>
</html>
```